Comprehensive guide for the front desk medical office staff.

selling a reference guide for the front desk personnel at Urgent Care clinics

Target Market(s)

Urgent Care and physian office manager s

Industry/Entity Type

Medical

```html
<!DOCTYPE html>
<html lang="en">
<head>
<meta charset="utf-8">
<title>Front Desk Reference Guide Poster</title>
<link rel="stylesheet" href="https://fonts.googleapis.com/css2?family=Roboto+Condensed:ital,wght@0,400;0,700;1,700&display=swap">
<style>
  :root {
    --navy: #04354f;
    --sky: #3fb2e6;
    --yellow: #ffd200;
    --white: #ffffff;
    --red: #e8432f;
    --backdrop: #e9eaec;
  }
  * { margin: 0; padding: 0; box-sizing: border-box; }
  html, body {
    width: 1200px; height: 1200px; overflow: hidden;
    background: var(--backdrop);
    font-family: "Roboto Condensed", "Arial Narrow", sans-serif;
  }
  .poster {
    position: absolute; left: 208px; top: 20px;
    width: 845px; height: 1250px;
    background: var(--navy);
    transform: scale(0.928); transform-origin: top left;
    overflow: hidden;
  }
  .poster-art { position: absolute; inset: 0; width: 845px; height: 1250px; }
  .centered { position: absolute; left: 0; width: 100%; text-align: center; }
  .author-line {
    top: 48px; display: flex; justify-content: center; align-items: center; gap: 20px;
    color: var(--white); font-weight: 700; font-size: 35px;
  }
  .author-line .rule { width: 192px; height: 10px;
    border-top: 2px solid var(--white); border-bottom: 2px solid var(--white); position: relative; }
  .author-line .rule::after { content: ""; position: absolute; left: 8px; right: 8px; top: 2px; border-top: 2px solid var(--white); }
  .kicker { top: 104px; color: var(--yellow); font-weight: 700; font-size: 41px; }
  .headline { top: 158px; color: var(--sky); font-weight: 700; font-size: 76px; line-height: 64px; }
  .subline { top: 294px; color: var(--sky); font-weight: 700; font-size: 31px; line-height: 43px; }
  .info-card {
    position: absolute; left: 178px; top: 532px; width: 193px; height: 263px;
    background: var(--navy); color: var(--white); text-align: center;
    box-shadow: 0 4px 4px rgba(0,0,0,.25);
    padding-top: 22px;
  }
  .info-card .card-title { color: var(--yellow); font-weight: 700; font-size: 23px; line-height: 26px; }
  .info-card .card-author { font-style: italic; font-weight: 700; font-size: 24px; margin-top: 18px; }
  .info-card .card-text { font-size: 18px; line-height: 23px; margin-top: 4px; }
  .buy-button {
    position: absolute; left: 172px; top: 830px; width: 195px; height: 47px;
    background: var(--red); color: var(--white); text-align: center;
    font-style: italic; font-weight: 700; font-size: 33px; line-height: 47px;
  }
  .feature-list { position: absolute; left: 98px; top: 942px; list-style: none; }
  .feature-list li {
    display: flex; align-items: center; gap: 10px;
    color: var(--white); font-weight: 700; font-size: 27px; line-height: 34px;
  }
  .feature-list svg { width: 27px; height: 24px; flex: none; }
  .order-call { top: 1096px; color: var(--white); font-weight: 700; font-size: 62px; line-height: 70px; }
  .price-line { top: 1160px; color: var(--yellow); font-weight: 700; font-size: 34px; }
</style>
</head>
<body>
<main class="poster">
  <svg class="poster-art" viewBox="0 0 845 1250" aria-hidden="false">
    <defs>
      <linearGradient id="photoTone" x1="0" y1="0" x2="1" y2="0">
        <stop offset="0" stop-color="#f1f1f1"/>
        <stop offset="0.5" stop-color="#e6e8ec"/>
        <stop offset="0.75" stop-color="#dcc6b4"/>
        <stop offset="1" stop-color="#e8c27a"/>
      </linearGradient>
    </defs>
    <path class="swoosh" fill="#ffd200" d="M0 520 C150 455 300 418 470 402 C300 432 150 490 0 562 Z"/>
    <path class="swoosh" fill="#ffd200" d="M845 768 C700 860 560 905 380 930 C560 912 710 872 845 800 Z"/>
    <path class="photo-area" role="img" aria-label="Photo of a smiling family of three in a bright room"
      fill="url(#photoTone)"
      d="M0 548 C180 460 460 390 845 458 L845 785 C620 895 300 950 0 875 Z"/>
  </svg>

  <div class="centered author-line"><span class="rule"></span><span>Laura Whitfield</span><span class="rule"></span></div>
  <div class="centered kicker">FRONT DESK REFERENCE GUIDE FOR</div>
  <h1 class="centered headline">URGENT CARE CENTERS<br>AND PHYSIAN OFFICES</h1>
  <p class="centered subline">Glossary of medical terminology used by front office<br>medical staff and insurance companies</p>

  <div class="info-card">
    <div class="card-title">DESK<br>INSURANCE<br>CARD</div>
    <div class="card-author">Laura Whitfield</div>
    <div class="card-text">shares over a decade<br>of medical office<br>experience in this<br>comprehensive guide.</div>
  </div>
  <div class="buy-button">BUY NOW</div>

  <ul class="feature-list">
    <li><svg viewBox="0 0 27 24"><path d="M2 13 L10 21 L25 3" fill="none" stroke="#ffd200" stroke-width="5"/></svg>Shows staff how to read an insurance card.</li>
    <li><svg viewBox="0 0 27 24"><path d="M2 13 L10 21 L25 3" fill="none" stroke="#ffd200" stroke-width="5"/></svg>What is a deductible and when to collect a copay.</li>
    <li><svg viewBox="0 0 27 24"><path d="M2 13 L10 21 L25 3" fill="none" stroke="#ffd200" stroke-width="5"/></svg>What is Workers comp.</li>
    <li><svg viewBox="0 0 27 24"><path d="M2 13 L10 21 L25 3" fill="none" stroke="#ffd200" stroke-width="5"/></svg>Information in HIPPA guidelines rance plans.</li>
  </ul>

  <div class="centered order-call">To order call 555-014-2290</div>
  <div class="centered price-line">Price is $99.99 plus $7.00 shipping and handling</div>
</main>
</body>
</html>
```